Law Firm Header Revision

Task: Redesign my law firm Word document header (modern, succinct, logo-first, easy address updates)

I need you to revise and modernize my Microsoft Word document header for Law Office of Bram Holcott, PLLC. The result should look professional and clean on letters (including Letters of Protection), with the logo as the main focus and the text kept succinct.

Goals:
1. Create a modern, minimal header that feels premium and uncluttered.
Make the logo the most visually dominant element.
Reduce the visual weight of the contact/address block so it doesn’t distract from the document.
Make the address easy to change later (I’m moving offices soon) while keeping the same header design.

2. Content to include (keep all info accurate):
Law Office of Bram Holcott, PLLC
615 Pemberly St. Ste #300-214, Houston, TX 77002
Office: 832.555.0143
Direct: 713.555.0187
Fax: 832.555.0129
Bholcottlaw.com

3. Layout requirements:
Provide 3 header style options:
Logo left + contact info right
Centered logo + single concise contact line below
Logo left + firm name prominent + minimal contact line
The primary line near the logo should be minimal (preferably website + main office phone).
The address should be easy to update in one place without redesigning the header. Prefer either:
Move the full address to the footer, or
Put the address in a single dedicated line/block so I can edit it once and keep the layout unchanged.
4. Build constraints:
Must be achievable using standard Microsoft Word tools only (header/footer, tables, alignment, fonts, spacing). No advanced graphics software.
Provide exact header text, plus step-by-step Word instructions for each option:
Font recommendations + sizes
Alignment
Spacing
Table setup (if used)
How to keep it consistent across pages

5. Deliverable:
For each of the 3 options, provide:
The exact header content (with line breaks)
Formatting specs (fonts, sizes, spacing)
Word build steps so I can recreate it reliably and keep the logo as the focal point.

```html
<!DOCTYPE html>
<html lang="en">
<head>
<meta charset="utf-8">
<title>Law Office of Bram Holcott, PLLC — Letterhead Options</title>
<link rel="stylesheet" href="https://fonts.googleapis.com/css2?family=Montserrat:wght@500;600;700&display=swap">
<style>
  :root {
    --backdrop: #434343;
    --paper: #ffffff;
    --navy: #0c1628;
    --navy-deep: #05080f;
    --mark-tint: #eff0ef;
    --ink: #0c1628;
    --rule: #c9ccd1;
  }
  html, body {
    margin: 0;
    width: 1200px;
    height: 574px;
    overflow: hidden;
    background: var(--backdrop);
  }
  .sheet {
    position: absolute;
    top: 36.3px;
    width: 354.5px;
    height: 500.7px;
    background: var(--paper);
    font-family: "Montserrat", Arial, sans-serif;
  }
  .sheet--left-logo { left: 30.7px; }
  .sheet--centered { left: 423.9px; }
  .sheet--firm-name { left: 816.5px; }
  .sheet svg { display: block; width: 100%; height: 100%; }
  .band { fill: var(--navy); }
  .band-deep { fill: url(#footerFade); }
  .firm-mark { fill: var(--ink); font-weight: 600; font-size: 15px; }
  .firm-mark-sub { fill: var(--ink); font-weight: 600; font-size: 8px; letter-spacing: 4px; }
  .firm-title { fill: var(--paper); font-weight: 600; font-size: 10.5px; }
  .contact { fill: var(--ink); font-weight: 500; font-size: 9.5px; }
  .foot-strong { fill: var(--ink); font-weight: 700; font-size: 8.4px; }
  .foot-label { fill: var(--ink); font-weight: 500; font-size: 8.4px; }
  .foot-tag { fill: var(--ink); font-weight: 500; font-size: 6px; letter-spacing: 1.6px; }
  .page-no { fill: var(--paper); font-weight: 500; font-size: 11px; }
  .foot-rule { stroke: var(--rule); stroke-width: 1; }
  .watermark-box { fill: var(--mark-tint); }
  .watermark-name { fill: var(--paper); font-weight: 600; font-size: 38px; }
  .icon-disc { fill: var(--navy); }
  .icon-glyph { fill: none; stroke: var(--paper); stroke-width: 1.4; }
  .icon-fill { fill: var(--paper); }
</style>
</head>
<body>

<svg width="0" height="0" style="position:absolute" aria-hidden="true">
  <defs>
    <linearGradient id="footerFade" x1="0" y1="0" x2="1" y2="0">
      <stop offset="0" stop-color="#05080f"/>
      <stop offset="1" stop-color="#18243a"/>
    </linearGradient>
    <symbol id="icon-office" viewBox="0 0 14 14">
      <circle class="icon-disc" cx="7" cy="7" r="7"/>
      <rect class="icon-glyph" x="4" y="3.5" width="6" height="7" rx="0.6"/>
      <line class="icon-glyph" x1="5.5" y1="6" x2="8.5" y2="6"/>
      <line class="icon-glyph" x1="5.5" y1="8" x2="8.5" y2="8"/>
    </symbol>
    <symbol id="icon-globe" viewBox="0 0 14 14">
      <circle class="icon-disc" cx="7" cy="7" r="7"/>
      <circle class="icon-glyph" cx="7" cy="7" r="3.8"/>
      <ellipse class="icon-glyph" cx="7" cy="7" rx="1.6" ry="3.8"/>
      <line class="icon-glyph" x1="3.2" y1="7" x2="10.8" y2="7"/>
    </symbol>
    <symbol id="icon-pin" viewBox="0 0 20 20">
      <circle class="icon-disc" cx="10" cy="10" r="10"/>
      <path class="icon-fill" d="M10 4.2a4 4 0 0 0-4 4c0 3 4 7.6 4 7.6s4-4.6 4-7.6a4 4 0 0 0-4-4zm0 5.6a1.6 1.6 0 1 1 0-3.2 1.6 1.6 0 0 1 0 3.2z"/>
    </symbol>
    <symbol id="icon-phone" viewBox="0 0 20 20">
      <circle class="icon-disc" cx="10" cy="10" r="10"/>
      <path class="icon-fill" d="M6.6 5.2l1.8-.4 1 2.6-1.2.9a6.6 6.6 0 0 0 3.4 3.4l.9-1.2 2.6 1-.4 1.8c-.1.5-.6.8-1.1.8A8.3 8.3 0 0 1 5.8 6.3c0-.5.3-1 .8-1.1z"/>
    </symbol>
    <symbol id="icon-fax" viewBox="0 0 20 20">
      <circle class="icon-disc" cx="10" cy="10" r="10"/>
      <rect class="icon-fill" x="7" y="4.5" width="6" height="3"/>
      <rect class="icon-fill" x="5" y="8" width="10" height="5" rx="1"/>
      <rect class="icon-disc" x="7" y="11" width="6" height="4.5"/>
      <rect class="icon-fill" x="7.6" y="11.6" width="4.8" height="3.4"/>
    </symbol>
  </defs>
</svg>

<!-- Option 1: logo left, contact right -->
<section class="sheet sheet--left-logo" aria-label="Option 1: logo left with contact information right">
  <svg viewBox="0 0 761 1075">
    <g class="header">
      <rect class="band" x="0" y="18" width="28" height="38"/>
      <rect class="band" x="38" y="20" width="32" height="35"/>
      <text class="firm-mark" x="76" y="40" textLength="112" lengthAdjust="spacing">BRAM HOLCOTT</text>
      <text class="firm-mark-sub" x="134" y="54" text-anchor="middle">LAW</text>
      <polygon class="band" points="199,18 516,18 504,56 199,56"/>
      <polygon class="band" points="522,18 532,18 520,56 510,56"/>
      <use href="#icon-office" x="542" y="20" width="13" height="13"/>
      <text class="contact" x="559" y="30" textLength="114" lengthAdjust="spacing">Office: 832.555.0143</text>
      <use href="#icon-globe" x="542" y="41" width="13" height="13"/>
      <text class="contact" x="559" y="51" textLength="130" lengthAdjust="spacingAndGlyphs">Website: Bholcottlaw.com</text>
      <polygon class="band" points="706,18 716,18 704,56 694,56"/>
      <polygon class="band" points="724,18 761,18 761,56 712,56"/>
    </g>

    <g class="watermark" role="img" aria-label="Faint firm name watermark">
      <rect class="watermark-box" x="227" y="390" width="307" height="294"/>
      <text class="watermark-name" x="380.5" y="550" text-anchor="middle">Holcott</text>
    </g>

    <g class="footer">
      <rect class="band" x="0" y="1068" width="761" height="7"/>
      <polygon class="band" points="0,1018 62,1018 112,1075 0,1075"/>
      <polygon class="band-deep" points="76,1018 124,1018 174,1075 126,1075"/>
      <use href="#icon-pin" x="164" y="1020" width="20" height="20"/>
      <text class="foot-strong" x="189" y="1026">Law Office of Bram Holcott, PLLC, 615 Pemberly</text>
      <text class="foot-strong" x="189" y="1040">St. Ste #300-214, Houston, TX 77002</text>
      <use href="#icon-phone" x="414" y="1020" width="20" height="20"/>
      <text class="foot-label" x="441" y="1026">Phone Number</text>
      <text class="foot-strong" x="441" y="1040">713.555.0187</text>
      <use href="#icon-fax" x="518" y="1020" width="20" height="20"/>
      <text class="foot-label" x="545" y="1026">Fax Number</text>
      <text class="foot-strong" x="545" y="1041">832.555.0129</text>
      <line class="foot-rule" x1="165" y1="1049" x2="606" y2="1049"/>
      <text class="foot-tag" x="385" y="1062" text-anchor="middle">LETTERS OF PROTECTION</text>
      <polygon class="band-deep" points="650,1018 700,1018 650,1075 602,1075"/>
      <polygon class="band" points="712,1018 761,1018 761,1075 662,1075"/>
      <text class="page-no" x="716" y="1056">01</text>
    </g>
  </svg>
</section>

<!-- Option 2: centered logo, contact line below -->
<section class="sheet sheet--centered" aria-label="Option 2: centered logo with a single contact line below">
  <svg viewBox="0 0 761 1075">
    <g class="header">
      <polygon class="band" points="0,18 250,18 238,56 0,56"/>
      <polygon class="band" points="256,18 266,18 254,56 244,56"/>
      <rect class="band" x="302" y="20" width="32" height="35"/>
      <text class="firm-mark" x="340" y="40" textLength="112" lengthAdjust="spacing">BRAM HOLCOTT</text>
      <text class="firm-mark-sub" x="398" y="54" text-anchor="middle">LAW</text>
      <polygon class="band" points="484,18 494,18 506,56 496,56"/>
      <polygon class="band" points="508,18 761,18 761,56 520,56"/>
      <use href="#icon-office" x="232" y="69" width="13" height="13"/>
      <text class="contact" x="249" y="79" textLength="114" lengthAdjust="spacing">Office: 832.555.0143</text>
      <use href="#icon-globe" x="381" y="69" width="13" height="13"/>
      <text class="contact" x="398" y="79" textLength="130" lengthAdjust="spacingAndGlyphs">Website: Bholcottlaw.com</text>
    </g>

    <g class="watermark" role="img" aria-label="Faint firm name watermark">
      <rect class="watermark-box" x="227" y="390" width="307" height="294"/>
      <text class="watermark-name" x="380.5" y="550" text-anchor="middle">Holcott</text>
    </g>

    <g class="footer">
      <rect class="band" x="0" y="1068" width="761" height="7"/>
      <polygon class="band" points="0,1018 62,1018 112,1075 0,1075"/>
      <polygon class="band-deep" points="76,1018 124,1018 174,1075 126,1075"/>
      <use href="#icon-pin" x="164" y="1020" width="20" height="20"/>
      <text class="foot-strong" x="189" y="1026">Law Office of Bram Holcott, PLLC 615</text>
      <text class="foot-strong" x="189" y="1040">Pemberly St. Ste #300-214, Houston,TX 77002</text>
      <use href="#icon-phone" x="411" y="1020" width="20" height="20"/>
      <text class="foot-label" x="438" y="1027">Phone Number</text>
      <text class="foot-strong" x="438" y="1040">713.555.0187</text>
      <use href="#icon-fax" x="518" y="1020" width="20" height="20"/>
      <text class="foot-label" x="545" y="1027">Fax Number</text>
      <text class="foot-strong" x="545" y="1040">832.555.0129</text>
      <line class="foot-rule" x1="165" y1="1049" x2="606" y2="1049"/>
      <text class="foot-tag" x="385" y="1062" text-anchor="middle">LETTERS OF PROTECTION</text>
      <polygon class="band-deep" points="650,1018 700,1018 650,1075 602,1075"/>
      <polygon class="band" points="712,1018 761,1018 761,1075 662,1075"/>
      <text class="page-no" x="716" y="1056">01</text>
    </g>
  </svg>
</section>

<!-- Option 3: logo left, firm name prominent -->
<section class="sheet sheet--firm-name" aria-label="Option 3: logo left with prominent firm name and minimal contact line">
  <svg viewBox="0 0 761 1075">
    <g class="header">
      <rect class="band" x="0" y="18" width="28" height="38"/>
      <rect class="band" x="38" y="20" width="32" height="35"/>
      <text class="firm-mark" x="76" y="40" textLength="112" lengthAdjust="spacing">BRAM HOLCOTT</text>
      <text class="firm-mark-sub" x="134" y="54" text-anchor="middle">LAW</text>
      <polygon class="band" points="199,18 516,18 504,56 199,56"/>
      <text class="firm-title" x="216" y="41" textLength="272" lengthAdjust="spacing">LAW OFFICE OF BRAM HOLCOTT, PLLC</text>
      <polygon class="band" points="522,18 532,18 520,56 510,56"/>
      <use href="#icon-office" x="542" y="20" width="13" height="13"/>
      <text class="contact" x="559" y="30" textLength="114" lengthAdjust="spacing">Office: 832.555.0143</text>
      <use href="#icon-globe" x="542" y="41" width="13" height="13"/>
      <text class="contact" x="559" y="51" textLength="130" lengthAdjust="spacingAndGlyphs">Website: Bholcottlaw.com</text>
      <polygon class="band" points="706,18 716,18 704,56 694,56"/>
      <polygon class="band" points="724,18 761,18 761,56 712,56"/>
    </g>

    <g class="watermark" role="img" aria-label="Faint firm name watermark">
      <rect class="watermark-box" x="227" y="390" width="307" height="294"/>
      <text class="watermark-name" x="380.5" y="550" text-anchor="middle">Holcott</text>
    </g>

    <g class="footer">
      <rect class="band" x="0" y="1068" width="761" height="7"/>
      <polygon class="band" points="0,1018 62,1018 112,1075 0,1075"/>
      <polygon class="band-deep" points="76,1018 124,1018 174,1075 126,1075"/>
      <use href="#icon-pin" x="164" y="1020" width="20" height="20"/>
      <text class="foot-strong" x="189" y="1026">615 Pemberly St. Ste #300-214,</text>
      <text class="foot-strong" x="189" y="1040">Houston,TX 77002</text>
      <use href="#icon-phone" x="372" y="1020" width="20" height="20"/>
      <text class="foot-label" x="399" y="1026">Phone Number</text>
      <text class="foot-strong" x="399" y="1040">713.555.0187</text>
      <use href="#icon-fax" x="513" y="1020" width="20" height="20"/>
      <text class="foot-label" x="540" y="1026">Fax Number</text>
      <text class="foot-strong" x="540" y="1041">832.555.0129</text>
      <line class="foot-rule" x1="165" y1="1049" x2="606" y2="1049"/>
      <text class="foot-tag" x="385" y="1062" text-anchor="middle">LETTERS OF PROTECTION</text>
      <polygon class="band-deep" points="650,1018 700,1018 650,1075 602,1075"/>
      <polygon class="band" points="712,1018 761,1018 761,1075 662,1075"/>
      <text class="page-no" x="716" y="1056">01</text>
    </g>
  </svg>
</section>

</body>
</html>
```